Business Card For Halvenmoor Financial Consulting

Hi, I would like a business card designed. Bold, modern.
Please use the same design as the logo. I have also attached the website design to see the overall theme.
Wordmark Font
Color: Hex: #01AEF7

```html
<!DOCTYPE html>
<html lang="en">
<head>
<meta charset="utf-8">
<title>Halvenmoor Financial Consulting – Business Card</title>
<link rel="stylesheet" href="https://fonts.googleapis.com/css2?family=Montserrat:wght@400;500;700;800&display=swap">
<style>
  :root {
    --card-bg: #14202b;
    --card-bg-light: #1d2c38;
    --accent: #01aef7;
    --accent-soft: #3aa8e0;
    --ink: #ffffff;
    --page: #e4e6e8;
  }
  * { margin: 0; padding: 0; box-sizing: border-box; }
  html, body {
    width: 1200px; height: 900px; overflow: hidden;
    background: var(--page);
    font-family: "Montserrat", sans-serif;
  }
  .canvas {
    width: 1200px; height: 900px;
    display: flex; flex-direction: column;
    align-items: center; justify-content: center; gap: 40px;
  }
  .card {
    width: 700px; height: 400px;
    background: linear-gradient(135deg, var(--card-bg-light) 0%, var(--card-bg) 60%);
    position: relative; color: var(--ink);
    box-shadow: 0 8px 24px rgba(0,0,0,0.25);
  }
  .brand {
    display: flex; align-items: center; gap: 16px;
  }
  .brand-square {
    border: 5px solid var(--accent);
    flex: none;
  }
  .brand-name {
    font-weight: 800; color: var(--ink);
    text-transform: uppercase; line-height: 1.05;
    letter-spacing: 0.04em;
  }
  /* front */
  .card-front { display: flex; align-items: center; justify-content: center; }
  .card-front .brand-square { width: 78px; height: 78px; }
  .card-front .brand-name { font-size: 34px; }
  /* back */
  .card-back .brand { position: absolute; top: 44px; right: 44px; gap: 10px; }
  .card-back .brand-square { width: 40px; height: 40px; border-width: 3px; }
  .card-back .brand-name { font-size: 17px; }
  .identity {
    position: absolute; left: 0; top: 150px;
    padding-left: 52px;
  }
  .identity-bar {
    position: absolute; left: 14px; top: 36px;
    width: 22px; height: 60px; background: var(--accent-soft);
  }
  .person-name {
    font-weight: 700; font-size: 34px; color: var(--accent-soft);
    text-transform: uppercase; letter-spacing: 0.01em;
  }
  .person-title { font-size: 22px; font-weight: 400; margin-top: 2px; }
  .contacts {
    position: absolute; left: 52px; bottom: 36px;
    list-style: none; display: flex; flex-direction: column; gap: 10px;
  }
  .contact { display: flex; align-items: center; gap: 12px; font-size: 19px; }
  .contact-icon { width: 28px; height: 28px; flex: none; }
  .address {
    position: absolute; right: 44px; bottom: 40px;
    text-align: right; font-size: 19px; line-height: 1.4; font-style: normal;
  }
</style>
</head>
<body>
<main class="canvas">
  <section class="card card-front" aria-label="Card front">
    <div class="brand">
      <span class="brand-square"></span>
      <span class="brand-name">Halvenmoor<br>Financial Consulting</span>
    </div>
  </section>

  <section class="card card-back" aria-label="Card back">
    <div class="brand">
      <span class="brand-square"></span>
      <span class="brand-name">Halvenmoor<br>Financial Consulting</span>
    </div>

    <div class="identity">
      <span class="identity-bar"></span>
      <h1 class="person-name">Elin Marsh</h1>
      <p class="person-title">Senior Consultant</p>
    </div>

    <ul class="contacts">
      <li class="contact">
        <svg class="contact-icon" viewBox="0 0 28 28" aria-hidden="true">
          <circle cx="14" cy="14" r="14" fill="var(--accent-soft)"/>
          <path d="M9 8c1-1 2-1 3 0l1.5 2c.5.7.3 1.4-.3 2l-.8.8c.8 1.7 2.1 3 3.8 3.8l.8-.8c.6-.6 1.3-.8 2-.3l2 1.5c1 1 1 2 0 3-1.5 1.5-4 1.5-7-1.3S7 10.5 9 8z" fill="#fff"/>
        </svg>
        <span>+1 555 014 2290</span>
      </li>
      <li class="contact">
        <svg class="contact-icon" viewBox="0 0 28 28" aria-hidden="true">
          <circle cx="14" cy="14" r="14" fill="var(--accent-soft)"/>
          <rect x="7" y="9" width="14" height="10" rx="1" fill="#fff"/>
          <path d="M7.5 9.5L14 15l6.5-5.5" fill="none" stroke="var(--accent-soft)" stroke-width="1.4"/>
        </svg>
        <span>info@halvenmoor.com</span>
      </li>
      <li class="contact">
        <svg class="contact-icon" viewBox="0 0 28 28" aria-hidden="true">
          <circle cx="14" cy="14" r="14" fill="var(--accent-soft)"/>
          <g fill="none" stroke="#fff" stroke-width="1.4">
            <circle cx="14" cy="14" r="7"/>
            <ellipse cx="14" cy="14" rx="3" ry="7"/>
            <path d="M7 14h14"/>
          </g>
        </svg>
        <span>www.halvenmoor.com</span>
      </li>
    </ul>

    <address class="address">42-07 Linden Ave 18<br>Westbrook, NY 11402</address>
  </section>
</main>
</body>
</html>
```